Pediatric Therapy Clinic Brochure

We need a Brochure for a new pediatric therapy clinic. The clinic offers occupational therapy, physical therapy, speech therapy and feeding therapy. We want a brochure for parents, doctors and medical professional. It should have a fun and inviting, but still professional feel. Should be kid focused, bright and colorful. All the text / wording is there and a rough layout. Now I need someone to tidy and jazz it up and make it look professional.

Target Market(s)

Parents, doctors, medical professional

Industry/Entity Type

Medical

Font styles to use
Serif
Sans Serif

Requirements
Must have
• Keep All the text with information about services the same. Logo on front. Pictures throughout (use any of the pictures provided) (try and match up with corresponding service) (pictures are labeled). Need to have Map and contact info
• Keep colors consistent with our logo
Nice to have
• Background, special effects. Make it look fancy and professional
Should not have
• Not so busy that is takes away from the text

```html
<!DOCTYPE html>
<html lang="en">
<head>
<meta charset="utf-8">
<title>Maple Creek Pediatric Therapy – Brochure Inside</title>
<link rel="stylesheet" href="https://fonts.googleapis.com/css2?family=Oswald:wght@500;600&family=Arimo:wght@400;700&display=swap">
<style>
  :root {
    --brand-blue: #1b5aa6;
    --brand-orange: #e8641e;
    --paper: #ffffff;
    --stage: #d6d6d6;
    --fold: #e6e6e6;
    --text-blue: #1f4f8f;
  }
  * { box-sizing: border-box; margin: 0; padding: 0; }
  html, body { width: 1200px; height: 1200px; overflow: hidden; }
  body {
    background: var(--stage);
    font-family: "Arimo", Arial, sans-serif;
    position: relative;
  }
  .brochure {
    position: absolute;
    left: 30px; top: 160px;
    width: 1140px; height: 880px;
    display: grid;
    grid-template-columns: repeat(3, 1fr);
    background: var(--paper);
    box-shadow: 0 10px 30px rgba(0,0,0,0.18);
  }
  .panel {
    position: relative;
    padding: 28px 34px;
    display: flex;
    flex-direction: column;
  }
  .panel + .panel { border-left: 1px solid var(--fold); }
  .panel--left { padding: 0 0 24px; }
  .service { margin-bottom: 22px; }
  .service__title {
    font-family: "Oswald", "Arial Narrow", sans-serif;
    font-weight: 600;
    color: var(--brand-blue);
    font-size: 30px;
    text-align: center;
    letter-spacing: 0.3px;
    line-height: 1.1;
    text-transform: uppercase;
  }
  .service__lede {
    color: var(--text-blue);
    font-size: 13.5px;
    line-height: 1.35;
    text-align: center;
    margin: 6px 10px 4px;
  }
  .swoosh { display: block; width: 100%; height: 14px; margin: 2px 0 10px; }
  .service__list {
    list-style: none;
    color: var(--brand-orange);
    font-weight: 700;
    font-size: 14px;
    line-height: 1.32;
  }
  .service__list li { position: relative; padding-left: 14px; }
  .service__list li::before {
    content: "•";
    position: absolute; left: 0; top: 0;
    font-size: 12px;
  }
  .photo {
    display: block;
    border-radius: 2px;
  }
  .photo--hero {
    height: 265px;
    background: linear-gradient(160deg, #f4efe9 0%, #f1d6c4 45%, #e9c2a0 70%, #f2ece6 100%);
  }
  .occupational { padding: 20px 34px 0; }
  .photo-row {
    margin-top: auto;
    display: grid;
    grid-template-columns: 1fr 1fr;
    gap: 14px;
    padding: 0 24px;
  }
  .photo--small { height: 170px; box-shadow: 0 2px 6px rgba(0,0,0,0.15); }
  .photo--pasta { background: linear-gradient(160deg, #f2f2f2 0%, #e7c9a6 45%, #c9573a 75%, #ededed 100%); }
  .photo--ball { background: linear-gradient(170deg, #f3f3f3 0%, #e4c3a8 35%, #c0261f 60%, #2547a8 100%); }
  .brand {
    margin-top: auto;
    display: flex;
    align-items: center;
    justify-content: center;
    gap: 12px;
    padding-bottom: 10px;
  }
  .brand__dot {
    width: 22px; height: 22px;
    border-radius: 50%;
    background: var(--brand-orange);
    flex: none;
  }
  .brand__name {
    font-family: "Arimo", Arial, sans-serif;
    font-weight: 700;
    color: var(--brand-blue);
    font-size: 24px;
    line-height: 1.1;
    text-align: center;
  }
  .note {
    margin-top: 10px;
    color: var(--brand-orange);
    font-size: 14px;
    text-align: center;
  }
</style>
</head>
<body>
  <main class="brochure">
    <section class="panel panel--left">
      <div class="photo photo--hero" role="img" aria-label="Photo of a smiling child holding up paint-covered hands"></div>
      <div class="service occupational">
        <h2 class="service__title">Occupational Therapy</h2>
        <p class="service__lede">Helping children build better self-esteem, confidence and independence in all the things they do.</p>
        <svg class="swoosh" viewBox="0 0 300 14" preserveAspectRatio="none" aria-hidden="true"><path d="M0 12 Q150 -2 300 6" fill="none" stroke="var(--brand-blue)" stroke-width="3"/></svg>
        <ul class="service__list">
          <li>Sensory Processing Disorder</li>
          <li>Balance, Coordination, Strength, and Endurance</li>
          <li>Fine Motor and Handwriting</li>
          <li>Visual- Motor Integration</li>
          <li>Play and Social Skills</li>
          <li>Feeding and Oral Motor Skills</li>
          <li>Self-Care</li>
          <li>Academic and Cognitive Skills</li>
          <li>Behavioral Difficulties</li>
          <li>Developmental Delays</li>
        </ul>
      </div>
      <div class="photo-row">
        <div class="photo photo--small photo--pasta" role="img" aria-label="Photo of a toddler playing with spaghetti and a bowl on the head"></div>
        <div class="photo photo--small photo--ball" role="img" aria-label="Photo of a smiling child leaning on a blue therapy ball"></div>
      </div>
    </section>

    <section class="panel panel--middle">
      <div class="service">
        <h2 class="service__title">Speech Therapy</h2>
        <p class="service__lede">Helping children speak, communicate and understand language.</p>
        <svg class="swoosh" viewBox="0 0 300 14" preserveAspectRatio="none" aria-hidden="true"><path d="M0 12 Q150 -2 300 6" fill="none" stroke="var(--brand-blue)" stroke-width="3"/></svg>
        <ul class="service__list">
          <li>Expressive and Receptive Language</li>
          <li>Speech and Language Developmental Milestones</li>
          <li>Articulation / Intelligibility</li>
          <li>Speech Fluency</li>
          <li>Pragmatics and Social Skills</li>
          <li>Literacy and Vocabulary</li>
          <li>Apraxia of Speech</li>
          <li>Augmentative and Alternative Communication</li>
          <li>Feeding and Oral Motor</li>
        </ul>
      </div>
      <div class="service">
        <h2 class="service__title">Sensory Integration</h2>
        <p class="service__lede">Gradually increasing play based activities to improve a child's nervous system. Helping children learn to self-regulate their emotions, behaviors and arousal levels.</p>
        <svg class="swoosh" viewBox="0 0 300 14" preserveAspectRatio="none" aria-hidden="true"><path d="M0 12 Q150 -2 300 6" fill="none" stroke="var(--brand-blue)" stroke-width="3"/></svg>
        <ul class="service__list">
          <li>Autism and ADHD</li>
          <li>Sensory Processing Disorder</li>
          <li>Poor Tolerance of Sensory Stimuli from the Environment</li>
          <li>Meltdowns and Tantrums</li>
          <li>Poor Balance/Body Awareness</li>
          <li>Poor Attention and Concentration</li>
          <li>Poor Self-Regulation</li>
          <li>Behavior and Social Difficulties</li>
          <li>Poor Motor Coordination and Motor Planning</li>
          <li>Aggression, Frustration or Avoidance Behaviors</li>
        </ul>
      </div>
      <div class="brand">
        <span class="brand__dot" aria-hidden="true"></span>
        <span class="brand__name">Maple Creek<br>Pediatric Therapy</span>
      </div>
    </section>

    <section class="panel panel--right">
      <div class="service">
        <h2 class="service__title">Feeding Therapy</h2>
        <p class="service__lede">Providing skilled assessment and intervention to children with feeding difficulties.</p>
        <svg class="swoosh" viewBox="0 0 300 14" preserveAspectRatio="none" aria-hidden="true"><path d="M0 12 Q150 -2 300 6" fill="none" stroke="var(--brand-blue)" stroke-width="3"/></svg>
        <ul class="service__list">
          <li>Food Aversions</li>
          <li>Food Refusal</li>
          <li>Very Picky Eating</li>
          <li>Avoidance of Certain Textures</li>
          <li>Gagging and Vomiting</li>
          <li>Oral Motor/ Chewing Difficulties</li>
          <li>Limited Diet/Food Repertoire</li>
        </ul>
      </div>
      <div class="service">
        <h2 class="service__title">Physical Therapy</h2>
        <p class="service__lede">Helping children move and interact within their environment smoothly and confidently.</p>
        <svg class="swoosh" viewBox="0 0 300 14" preserveAspectRatio="none" aria-hidden="true"><path d="M0 12 Q150 -2 300 6" fill="none" stroke="var(--brand-blue)" stroke-width="3"/></svg>
        <ul class="service__list">
          <li>Torticollis</li>
          <li>Walking and Mobility</li>
          <li>Developmental Motor Milestones</li>
          <li>Balance, Coordination, Motor Planning</li>
          <li>Strength, Muscle Tone and Range of Motion</li>
          <li>Sports Injuries</li>
          <li>Toe Walking</li>
          <li>Myofascial Release</li>
          <li>Postural Control and Positioning</li>
        </ul>
      </div>
      <div class="service">
        <h2 class="service__title">Group Therapy</h2>
        <p class="service__lede">Using peer role models to learn new and challenging skills.</p>
        <svg class="swoosh" viewBox="0 0 300 14" preserveAspectRatio="none" aria-hidden="true"><path d="M0 12 Q150 -2 300 6" fill="none" stroke="var(--brand-blue)" stroke-width="3"/></svg>
        <ul class="service__list">
          <li>Social Groups</li>
          <li>Feeding Groups</li>
        </ul>
        <p class="note">**More Group Classes Coming Soon</p>
      </div>
    </section>
  </main>
</body>
</html>
```